Design a New Business Card for Our Company

We are looking for fresh, unique, and a modern business card that reflects our roots as digital marketing agency focused on SEM.

Industry/Entity Type

Marketing

Contact Information for Business Card

looking for very unique out of the box designs. clean and modern that compliments our logo

Requirements
Must have
• colors should match our logo
• Front should have name, address, email, and phone/fax of the person, phone/fax are the same number
• back should have our url

```html
<!DOCTYPE html>
<html lang="en">
<head>
<meta charset="utf-8">
<title>Clearwave – Business Cards</title>
<link rel="stylesheet" href="https://fonts.googleapis.com/css2?family=Nunito:wght@400;600;800&display=swap">
<style>
  :root {
    --bg: #e6e7e9;
    --card: #ffffff;
    --grey: #a8a9ab;
    --grey-light: #c9cacc;
    --blue: #5b9bd5;
    --ink: #2b2b2b;
    --shadow: rgba(0, 0, 0, 0.18);
  }
  * { box-sizing: border-box; margin: 0; padding: 0; }
  html, body {
    width: 1200px; height: 878px; overflow: hidden;
    background: var(--bg);
    font-family: "Nunito", Arial, sans-serif;
  }
  .stage {
    position: relative; width: 1200px; height: 878px;
    display: flex; align-items: center; justify-content: center; gap: 60px;
  }
  .card {
    position: relative; width: 525px; height: 300px;
    background: var(--card); overflow: hidden;
    box-shadow: 0 10px 28px var(--shadow);
  }

  /* Back of card */
  .back-top-band { position: absolute; left: 0; top: 0; width: 100%; height: 46px; background: var(--grey-light); }
  .back-bottom-band { position: absolute; left: 0; bottom: 0; width: 100%; height: 48px; background: var(--blue); }
  .back-wordmark {
    position: absolute; left: 70px; top: 92px;
    font-weight: 800; font-size: 64px; line-height: 1; color: var(--blue);
  }
  .back-url {
    position: absolute; left: 72px; top: 182px;
    font-size: 17px; font-weight: 600; color: var(--ink);
  }

  /* Front of card */
  .front-shape { position: absolute; left: 0; top: 0; width: 525px; height: 300px; }
  .front-header {
    position: absolute; right: 0; top: 22px; width: 230px; height: 40px; background: var(--grey);
    display: flex; align-items: center; padding-left: 18px;
  }
  .front-wordmark { font-weight: 800; font-size: 26px; color: #ffffff; line-height: 1; }
  .front-accent { position: absolute; right: 0; top: 70px; width: 110px; height: 6px; background: var(--blue); }
  .front-details { position: absolute; left: 250px; top: 82px; width: 260px; color: var(--ink); }
  .person-name { font-size: 26px; font-weight: 600; color: var(--blue); line-height: 1.1; }
  .person-title { font-size: 13px; margin: 4px 0 14px; }
  .contact-line { font-size: 13px; line-height: 1.5; white-space: nowrap; }
  .contact-line .label { color: var(--blue); font-weight: 600; }
  .contact-line .gap { display: inline-block; width: 26px; }
  .address { margin-top: 10px; font-size: 13px; line-height: 1.4; }
</style>
</head>
<body>
<main class="stage">

  <section class="card card-back" aria-label="Business card back">
    <div class="back-top-band"></div>
    <p class="back-wordmark">clearwave</p>
    <p class="back-url">www.clearwave-sem.net</p>
    <div class="back-bottom-band"></div>
  </section>

  <section class="card card-front" aria-label="Business card front">
    <svg class="front-shape" viewBox="0 0 525 300" aria-hidden="true">
      <polygon points="0,0 175,0 0,300" fill="#c9cacc"/>
    </svg>
    <div class="front-header"><span class="front-wordmark">clearwave</span></div>
    <div class="front-accent"></div>
    <div class="front-details">
      <h1 class="person-name">Your Name</h1>
      <p class="person-title">Job Title</p>
      <p class="contact-line"><span class="label">P:</span> 555 0142<span class="gap"></span><span class="label">F:</span> 555 0142</p>
      <p class="contact-line"><span class="label">E:</span> hello@clearwave-sem.net</p>
      <p class="address">48 Harbor Lane, Suite 3<br>PO Box 220, Millbrook</p>
    </div>
  </section>

</main>
</body>
</html>
```